Custom Woodworking and Rock Design

We specialize in original, high quality, wood and rock art. It’s should be self explanatory ask questions if you need. Your team designing a logo. Furniture is custom made to order. Rocks are designed depending on consumer needs. Wood and rock can also be combined for custom work. Painted rocks on vintage wood. Custom chairs and cabinets. Artistic rocks for multiple uses:garden, magnets, custom. All ideas and requests are welcome.

Target Market(s)

All

Contact Information for Business Card

Mara Voss
Talbertstonecraft@mailbrook.net

Font styles to use
Sans Serif

Requirements
Must have
• Clear lettering
Nice to have
• Eye catching
Should not have
• Blurr

```html
<!DOCTYPE html>
<html lang="en">
<head>
<meta charset="utf-8">
<title>Talbert Stone Art and joinery – Business Card</title>
<link href="https://fonts.googleapis.com/css2?family=Lato:wght@400;700&display=swap" rel="stylesheet">
<style>
  :root {
    --backdrop: #e9e9eb;
    --card: #ffffff;
    --ink: #6f7073;
    --ink-soft: #8a8b8e;
    --mark: #c9cacc;
    --swoosh: #d3d4d6;
    --pebble-a: #fbfbfb;
    --pebble-b: #eeeeef;
  }
  * { box-sizing: border-box; margin: 0; padding: 0; }
  html, body { width: 1200px; height: 880px; overflow: hidden; }
  body {
    background: var(--backdrop);
    font-family: "Lato", sans-serif;
    position: relative;
  }
  .card {
    position: absolute;
    width: 580px;
    height: 330px;
    background: var(--card);
    border-radius: 22px;
    overflow: hidden;
    box-shadow: 0 10px 28px rgba(0,0,0,0.18);
  }
  .card--front { left: 60px; top: 80px; }
  .card--back { left: 560px; top: 470px; }

  .swooshes { position: absolute; inset: 0; }

  .company-name {
    position: absolute;
    left: 40px; top: 120px;
    font-size: 26px;
    font-weight: 700;
    line-height: 1.15;
    color: var(--ink);
  }
  .brand-lockup {
    position: absolute;
    display: flex;
    flex-direction: column;
    align-items: center;
    gap: 10px;
    color: var(--mark);
    font-weight: 700;
    text-align: center;
    text-transform: uppercase;
    letter-spacing: 0.04em;
  }
  .brand-lockup__square { background: var(--mark); }
  .card--front .brand-lockup { right: 36px; top: 28px; font-size: 11px; line-height: 1.3; }
  .card--front .brand-lockup__square { width: 62px; height: 62px; }

  .contact {
    position: absolute;
    left: 40px; top: 226px;
    color: var(--ink);
  }
  .contact__name { font-size: 22px; font-weight: 700; line-height: 1.1; }
  .contact__role { font-size: 13px; color: var(--ink-soft); margin-top: 2px; }
  .contact__email { font-size: 15px; margin-top: 8px; }

  .pebble-field {
    position: absolute; inset: 0;
    background: radial-gradient(circle at 50% 50%, var(--pebble-a) 0%, var(--pebble-b) 100%);
  }
  .card--back .brand-lockup {
    left: 50%; top: 50%;
    transform: translate(-50%, -50%);
    font-size: 14px; line-height: 1.3;
  }
  .card--back .brand-lockup__square { width: 90px; height: 90px; }
</style>
</head>
<body>
  <section class="card card--front" aria-label="Business card front">
    <svg class="swooshes" viewBox="0 0 580 330" aria-hidden="true">
      <path d="M40 110 C 180 30, 420 20, 580 150" fill="none" stroke="var(--swoosh)" stroke-width="22" opacity="0.7"/>
      <path d="M300 -10 C 420 80, 380 230, 330 340" fill="none" stroke="var(--swoosh)" stroke-width="28" opacity="0.7"/>
    </svg>
    <h1 class="company-name">Talbert Stone Art<br>and joinery</h1>
    <div class="brand-lockup">
      <span class="brand-lockup__square"></span>
      <span>Talbert Stone<br>Art and Joinery</span>
    </div>
    <div class="contact">
      <p class="contact__name">Mara Voss</p>
      <p class="contact__role">Stone designer</p>
      <p class="contact__email">Talbertstonecraft@mailbrook.net</p>
    </div>
  </section>

  <section class="card card--back" aria-label="Business card back">
    <div class="pebble-field" role="img" aria-label="Scattered outlined pebble shapes pattern in light grey"></div>
    <div class="brand-lockup">
      <span class="brand-lockup__square"></span>
      <span>Talbert Stone<br>Art and Joinery</span>
    </div>
  </section>
</body>
</html>
```